Looking for 5 screen mockup's for an automotive web app

We are starting the process of a redesign for an automobile customization tool for car dealerships called Trim Option Builder. We are looking to improve the look and user experience while still keeping the existing functionality of the site so far.
We are uploading screenshots of the site as it stands today. We are looking for a clean, easy to navigate and flexible user interface.
Screen 1: Salesman Login: We are looking to clean up the login pages for the users. Both the login screen, and the page displayed once a user is logged in. We would like to make it easier for the user to start a presentation and make it easier for them to view their recent orders. We are thinking of using the empty space in the middle for two big buttons, one for a new order, one for viewing their orders list.
Screen 2: Vehicle Selection Screen: We are looking to minimize the steps needed to select a vehicle's Year, Make, Model, Trim and Color. Currently the site loads 5 separate pages (one for each step) in order to finalize vehicle selection. We would like to minimize this into less than 3 steps while still making it interactive and easy to choose a vehicle quickly.
Screen 3: Product Category Screen: This screen is what is displayed once a customer's vehicle has been selected. We would like to keep it similar to how to is, while improving the overall look of this screen. We would like to keep a dealership's image and a photo of the selected vehicle at the top of the page since the products displayed are an exact fit for that specific selected vehicle.
Screen 4: Product Grid Screen: This screen is what displays once a user selects a category from the previous screen. We would like to display products in a clean, readable and intriguing way. These products are being presented to people who are purchasing a vehicle/accessories from a new car dealership. So we would like to make sure they are interested in viewing the products.
Screen 5: Product Pop-Up Module: This displays a product's details and image currently. We would like to add more information to products to provide more information to the customer. We would like to be able to add a ClipNest video embed, an attachment button of some sorts, room for a longer and better description and an add to cart button.
Assets: I will upload a .zip file containing current screenshots, page briefs, and a video walkthrough of the flow of the website.
Target Market(s)
automotive
Industry/Entity Type
Car Accessorie
Number of Pages Required
5+ page
Font styles to use

```html
<!DOCTYPE html>
<html lang="en">
<head>
<meta charset="utf-8">
<title>Sign In – Northgate Motors</title>
<link rel="stylesheet" href="https://fonts.googleapis.com/css2?family=Roboto:wght@400;500;700&family=Arimo:wght@400&display=swap">
<style>
  :root {
    --ink: #1d1d1d;
    --muted: #333333;
    --line: #d9d9d9;
    --field-line: #a9a9a9;
    --rule: #b5b5b5;
    --accent: #2590f0;
    --brand: #c8202a;
    --paper: #ffffff;
  }
  * { box-sizing: border-box; margin: 0; padding: 0; }
  html, body {
    width: 1200px; height: 720px; overflow: hidden;
    background: var(--paper); color: var(--ink);
    font-family: "Roboto", Arial, sans-serif;
  }
  .page { position: relative; width: 1200px; height: 720px; }

  .dealer-brand {
    position: absolute; top: 46px; left: 0; width: 1200px;
    display: flex; justify-content: center; align-items: center; gap: 10px;
  }
  .dealer-brand__dot { width: 26px; height: 26px; border-radius: 50%; background: var(--brand); }
  .dealer-brand__name { font-size: 28px; font-weight: 700; color: var(--ink); letter-spacing: -0.5px; }

  .signin-card {
    position: absolute; left: 360px; top: 137px; width: 480px; height: 320px;
    border: 1px solid var(--line); background: var(--paper);
  }
  .signin-card__title {
    margin-top: 28px; text-align: center; line-height: 26px;
    font-size: 21px; font-weight: 700; color: var(--ink);
  }
  .signin-form { width: 240px; margin: 29px auto 0; }
  .field {
    display: flex; align-items: center; height: 32px;
    border: 1px solid var(--field-line); margin-bottom: 16px;
  }
  .field__icon { width: 42px; display: flex; justify-content: center; }
  .field__input {
    flex: 1; border: 0; outline: 0; background: transparent;
    font: 400 14px "Roboto", Arial, sans-serif; color: var(--muted);
  }
  .field__input::placeholder { color: var(--muted); }
  .signin-button {
    display: block; width: 240px; height: 40px; margin-top: 32px;
    border: 0; background: var(--accent); color: #fff;
    font: 500 20px "Roboto", Arial, sans-serif;
    box-shadow: 0 2px 3px rgba(0,0,0,0.18);
  }
  .product-mark {
    position: absolute; left: 0; top: 287px; width: 100%;
    display: flex; justify-content: center; align-items: center; gap: 6px;
  }
  .product-mark__square { width: 12px; height: 12px; background: var(--ink); }
  .product-mark__name { font-size: 12px; font-weight: 500; color: var(--ink); }

  .footer-rule {
    position: absolute; left: 24px; top: 592px; width: 1152px;
    border: 0; border-top: 1px solid var(--rule);
  }
  .site-footer {
    position: absolute; top: 621px; left: 0; width: 1200px; text-align: center;
    font: 400 12px "Arimo", Arial, sans-serif; color: var(--ink);
  }
</style>
</head>
<body>
<div class="page">
  <header class="dealer-brand">
    <span class="dealer-brand__dot"></span>
    <span class="dealer-brand__name">Northgate Motors</span>
  </header>

  <main class="signin-card">
    <h1 class="signin-card__title">Sign In to your Account</h1>
    <form class="signin-form">
      <label class="field">
        <span class="field__icon">
          <svg width="16" height="16" viewBox="0 0 24 24" aria-hidden="true"><path fill="#1d1d1d" d="M12 12c2.7 0 4.8-2.1 4.8-4.8S14.7 2.4 12 2.4 7.2 4.5 7.2 7.2 9.3 12 12 12zm0 2.4c-3.2 0-9.6 1.6-9.6 4.8v2.4h19.2v-2.4c0-3.2-6.4-4.8-9.6-4.8z"/></svg>
        </span>
        <input class="field__input" type="email" placeholder="Email ID">
      </label>
      <label class="field">
        <span class="field__icon">
          <svg width="20" height="14" viewBox="0 0 28 16" aria-hidden="true"><circle cx="6" cy="8" r="5" fill="none" stroke="#1d1d1d" stroke-width="3"/><rect x="10" y="6.5" width="17" height="3" fill="#1d1d1d"/><rect x="19" y="8" width="3" height="5" fill="#1d1d1d"/><rect x="24" y="8" width="3" height="5" fill="#1d1d1d"/></svg>
        </span>
        <input class="field__input" type="password" placeholder="Password">
      </label>
      <button class="signin-button" type="button">Sign In</button>
    </form>
    <div class="product-mark">
      <span class="product-mark__square"></span>
      <span class="product-mark__name">Trim Option Builder</span>
    </div>
  </main>

  <hr class="footer-rule">
  <footer class="site-footer">© Keystone Auto Group 2016. All Rights Reserved. Product of Keystone Dealers. Powered With Vector Core Engine (VCE)</footer>
</div>
</body>
</html>
```